Business Card Design

educational services
broker of essential services
So I love my The Velvet Kettle cards. I love the background.
I like the background on the copper valley card
I like a little part of each Meridel card
I want my card to stand out and be professional
I would also like somewhat of a brand
I do not want it to be specific to anything but the world and galaxy
I would like to be able to be used for everything, all encompassing
In spanish Cielo abierto, not sureother languages but i will do programs for other countries like China, Japan and Korea
Reason: It has been the first week of school and I have not been able to get the feedback I need.
Please change colors to Blue and GOld
Please add ~ over the n in Lorna
Please submit some vertical designs
Please include the world
Please make eagle a watermark
Make sure the Open Horizon doesnt have "preparatory school" under it
I am open to new designs and I will pay more after I chose a designer who seems to get all this stuff in my head!
Reason: Last minute designs were wonderful
Reason: I was out of town and not able to review the wonderful designs posted. I am narrowing the designs down now! I appreciate all the work done thus far.
Hello,
Thank you for all the designs. This is difficult. I have not been able to access them as I was able to last week so please be patient. If you also do web design please send me a message.
Again, thank you. I am down to just a few designs.
Sincerely,
Lorna Vickers Dunmore
I have been extremely busy, I should pick a design by the ned of this week. Thank you for your patience
Industry/Entity Type
Business
Contact Information for Business Card
Dr. Lorna Vickers Dunmore
www.ohacad.example
(555) 284-9306 US
lornajeanvickers@mailbox.example

```html
<!DOCTYPE html>
<html lang="en">
<head>
<meta charset="utf-8">
<title>Open Horizon — Business Card</title>
<link rel="stylesheet" href="https://fonts.googleapis.com/css2?family=Lobster&family=Open+Sans:wght@400;600;700&display=swap">
<style>
  :root {
    --page: #d9d9db;
    --card-front: #bde0f5;
    --navy: #0b2f6b;
    --royal: #0f4ea3;
    --deep: #06275e;
    --gold: #f2c12e;
    --gold-dark: #c8961a;
    --ink: #1d3e74;
    --link: #2a6fc2;
    --watermark: #9fc2d9;
    --globe-pale: #eaf4fb;
    --globe-blue: #5a95cc;
  }
  * { box-sizing: border-box; margin: 0; padding: 0; }
  html, body { width: 1200px; height: 1011px; overflow: hidden; }
  body {
    background: var(--page);
    font-family: "Open Sans", Arial, sans-serif;
    position: relative;
  }
  .card {
    position: absolute;
    top: 206px;
    width: 340px;
    height: 595px;
    overflow: hidden;
    box-shadow: 0 4px 14px rgba(0,0,0,.18);
  }

  /* Front */
  .card--front { left: 170px; background: var(--card-front); }
  .brand-band {
    position: absolute; left: 0; right: 0; top: 34px; height: 96px;
    background: linear-gradient(90deg, var(--deep), var(--royal) 55%, var(--navy));
    border-top: 4px solid var(--gold);
    border-bottom: 4px solid var(--gold);
    display: flex; align-items: center; gap: 12px;
    padding-left: 24px;
  }
  .brand-dot {
    width: 36px; height: 36px; border-radius: 50%;
    background: var(--royal); border: 2px solid #ffffff;
    flex: none;
  }
  .brand-name {
    color: #ffffff; font-weight: 700; font-size: 34px;
    letter-spacing: 1px; text-transform: uppercase;
  }
  .watermark {
    position: absolute; left: 44px; top: 190px; width: 260px; height: 120px;
    background: radial-gradient(ellipse at center, var(--watermark) 0%, rgba(159,194,217,0) 70%);
  }
  .holder {
    position: absolute; left: 30px; top: 400px;
    color: var(--ink); font-weight: 700; font-size: 19px;
  }
  .contacts {
    position: absolute; left: 30px; top: 444px;
    list-style: none; display: grid; gap: 12px;
  }
  .contacts li {
    display: flex; align-items: center; gap: 12px;
    color: var(--link); font-size: 15.5px;
  }
  .contacts svg { width: 20px; height: 20px; flex: none; }

  /* Back */
  .card--back {
    left: 690px;
    background: radial-gradient(circle at 50% 48%, #2f73c4 0%, var(--royal) 35%, var(--deep) 100%);
  }
  .globe {
    position: absolute; left: 40px; top: 167px; width: 260px; height: 260px;
    border-radius: 50%;
    background: radial-gradient(circle at 42% 45%, var(--globe-pale) 0%, #cfe4f4 55%, var(--globe-blue) 100%);
  }
  .tagline {
    position: absolute; left: 0; right: 0; top: 232px;
    text-align: center;
    font-family: "Lobster", cursive;
    font-size: 30px; line-height: 1.22;
    color: var(--navy);
    -webkit-text-stroke: 1px var(--gold-dark);
    text-shadow: 0 0 2px var(--gold), 1px 1px 0 var(--gold);
  }
</style>
</head>
<body>
  <section class="card card--front" aria-label="Business card front">
    <header class="brand-band">
      <span class="brand-dot"></span>
      <span class="brand-name">Open Horizon</span>
    </header>
    <div class="watermark" role="img" aria-label="Faint eagle in flight watermark"></div>
    <p class="holder">Dr. Lorna Vickers Dunmore</p>
    <ul class="contacts">
      <li>
        <svg viewBox="0 0 20 20" aria-hidden="true"><circle cx="10" cy="10" r="10" fill="#2a6fc2"/><path d="M7 5.5l2 2-1 1.2c.6 1.4 1.6 2.4 3 3l1.2-1 2 2-1.2 1.5C10 14 6 10 5.5 6.7z" fill="#fff"/></svg>
        (555) 284-9306 US
      </li>
      <li>
        <svg viewBox="0 0 20 20" aria-hidden="true"><circle cx="10" cy="10" r="10" fill="#2a6fc2"/><rect x="5" y="6.5" width="10" height="7" rx="1" fill="#fff"/><path d="M5.5 7l4.5 3.5L14.5 7" stroke="#2a6fc2" stroke-width="1.2" fill="none"/></svg>
        lornajeanvickers@mailbox.example
      </li>
      <li>
        <svg viewBox="0 0 20 20" aria-hidden="true"><circle cx="10" cy="10" r="10" fill="#2a6fc2"/><circle cx="10" cy="10" r="5" stroke="#fff" stroke-width="1.3" fill="none"/><ellipse cx="10" cy="10" rx="2" ry="5" stroke="#fff" stroke-width="1.1" fill="none"/><path d="M5 10h10" stroke="#fff" stroke-width="1.1"/></svg>
        www.ohacad.example
      </li>
    </ul>
  </section>

  <section class="card card--back" aria-label="Business card back">
    <div class="globe" role="img" aria-label="World map inside a pale globe"></div>
    <p class="tagline">Where there are<br>Open Horizon to<br>Your Success!</p>
  </section>
</body>
</html>
```